Flat bootstrap design for existing site

I'm looking for a modern flat design based around an existing logo. This has to be a custom design (no external templates), and implemented into a bootstrap framework.

The logo is attached as 2 versions - choose whichever you want, that flows better with whatever design you choose.

Added screenshots of the existing site (currently using the default bootstrap layouts). Please make your designs around those pages in the screenshots (i.e. the homepage only has the postal code input and the header). The active page has 3 screenshots, because I wanted to illustrate the other states that would be visible (in the table rows).

This is a moving/junk removal website, just for some context.

Here's some example websites (flat designs) that I like, just to give you an idea of what I'm after.

https://www.plimvora.com/
https://dacklow.com/
https://trevanu.com/
https://quobrintal.com/en/

Coding

Coded - Design and coding required

Number of Pages Required

5+ page

Colors

Designer to choose colors to be used in the design.

Requirements
Must have
• It must be a modern/simple flat design, that is built around the existing logo (attached).
• It has to be implemented using bootstrap.

```html
<!DOCTYPE html>
<html lang="en">
<head>
<meta charset="utf-8">
<title>Haulbeam – Booking</title>
<link href="https://fonts.googleapis.com/css2?family=Roboto:wght@400;500;700&display=swap" rel="stylesheet">
<style>
:root{
  --sky:#49c8f5;
  --sky-band:rgba(58,170,220,.85);
  --panel:rgba(45,45,50,.72);
  --white:#ffffff;
  --line:rgba(255,255,255,.75);
  --pending:#e60d0d;
}
*{box-sizing:border-box;margin:0;padding:0}
html,body{width:1200px;height:1114px;overflow:hidden}
body{position:relative;font-family:'Roboto',sans-serif;color:var(--white);font-size:13px}
.backdrop{position:absolute;left:0;top:101px;width:1200px;height:1013px;
  background:radial-gradient(ellipse at 70% 40%,#7a5a4a 0%,#3e3a3c 45%,#2a3a55 80%),linear-gradient(#5a4238,#2d3c58)}
.site-header{position:absolute;left:0;top:0;width:1200px;height:101px;background:var(--sky)}
.brand{position:absolute;left:110px;top:30px;display:flex;align-items:center;gap:10px;font-size:30px;font-weight:700;letter-spacing:1px}
.brand-mark{width:18px;height:18px;border-radius:50%;background:var(--white)}
.nav a{position:absolute;color:var(--white);text-decoration:none;font-size:13.5px;font-weight:500;top:43px}
.nav .become{top:34px;left:782px;width:133px;height:33px;background:var(--white);color:var(--sky);border-radius:3px;text-align:center;line-height:33px}
.account{position:absolute;left:964px;top:43px;font-size:13.5px;font-weight:500}
.panel{position:absolute;left:99px;width:1002px;background:var(--panel)}
.booking{top:156px;height:378px}
.abs{position:absolute}
.title-sm{left:26px;top:26px;font-size:14px;font-weight:500;display:flex;gap:10px;align-items:center}
.label{font-size:14px}
.field{border:1px solid var(--white);border-radius:5px;font-size:14px;padding:0 16px;display:flex;align-items:center}
.cal-btn{position:absolute;right:3px;top:2px;width:51px;height:35px;background:var(--sky);border-radius:4px;display:flex;align-items:center;justify-content:center}
.btn-update{left:27px;top:307px;width:130px;height:44px;background:var(--sky);border-radius:5px;font-size:14.5px;font-weight:500;display:flex;align-items:center;justify-content:center}
.rule{position:absolute;left:99px;width:1002px;height:1px;background:var(--line)}
.drivers{top:585px;height:455px}
.drivers h2{position:absolute;left:8px;top:28px;font-size:19.5px;font-weight:400}
.notice{position:absolute;left:0;top:68px;width:1002px;height:51px;background:var(--sky-band);border-bottom:1px solid var(--sky);padding-left:28px;line-height:51px;font-size:12.5px}
.row{position:absolute;left:0;width:1002px;border-bottom:1px solid rgba(255,255,255,.6);font-size:12.5px}
.row span{position:absolute}
.pending{position:absolute;right:0;width:118px;height:28px;background:var(--pending);border-radius:5px;text-align:center;line-height:28px;font-size:12.5px}
.footer{position:absolute;left:0;width:1200px;top:1080px;text-align:center;font-size:12.5px;font-weight:500}
</style>
</head>
<body>
<div class="backdrop" role="img" aria-label="Background photo of a smiling man working at a laptop"></div>

<header class="site-header">
  <div class="brand"><span class="brand-mark"></span>HAULBEAM</div>
  <nav class="nav">
    <a href="#" style="left:566px">BOOK</a>
    <a href="#" style="left:645px">HOW IT WORKS</a>
    <a href="#" class="become">BECOME A DRIVER</a>
  </nav>
  <div class="account">dana@moverlane.com &#9662;</div>
</header>

<section class="panel booking">
  <div class="abs title-sm">
    <svg width="13" height="13" viewBox="0 0 14 14" fill="none" stroke="#fff" stroke-width="1.5"><path d="M6 2H2v10h10V8"/><path d="M5 9l1-3 6-5 2 2-6 5z"/></svg>
    Booking Details</div>
  <div class="abs label" style="left:26px;top:59px">Package Selected :</div>
  <div class="abs label" style="left:508px;top:59px">Pick-up time&nbsp; Selected :</div>
  <div class="abs field" style="left:27px;top:96px;width:464px;height:39px">Package 1
    <svg style="position:absolute;right:18px" width="8" height="12" viewBox="0 0 8 12" fill="#fff"><path d="M4 0l4 4H0zM4 12L0 8h8z"/></svg></div>
  <div class="abs field" style="left:509px;top:96px;width:463px;height:39px">July 20 at 4.30 pm
    <div class="cal-btn"><svg width="16" height="16" viewBox="0 0 16 16" fill="none" stroke="#fff" stroke-width="1.3"><rect x="1.5" y="3" width="13" height="11.5"/><path d="M1.5 6.5h13M5 1.5v3M11 1.5v3M5.5 6.5v8M10.5 6.5v8M1.5 10.5h13"/></svg></div></div>
  <div class="abs label" style="left:26px;top:165px">Description :</div>
  <div class="abs field" style="left:27px;top:195px;width:948px;height:83px;align-items:flex-start;padding:13px 12px">1 large Stove</div>
  <div class="abs btn-update">UPDATE</div>
</section>

<div class="rule" style="top:560px"></div>

<section class="panel drivers">
  <h2>Drivers In Your Area</h2>
  <div class="notice">Please Stay&nbsp; On this Page and be patient, While we contact the drivers and find you one ASAP.</div>
  <div class="row" style="top:119px;height:50px"><span style="left:13px;top:22px">Name</span><span style="left:245px;top:22px">Distance (km)</span><span style="left:520px;top:22px">Agreed Pick-up time</span></div>
  <div class="row" style="top:169px;height:52px"><span style="left:12px;top:23px">Marcus Pell</span><span style="left:244px;top:23px">4.04 km away</span><span style="left:548px;top:23px">-</span><div class="pending" style="top:16px">Pending</div></div>
  <div class="row" style="top:221px;height:64px"><span style="left:12px;top:36px">Owen Rask</span><span style="left:241px;top:36px">5.23 km away</span><span style="left:548px;top:36px">-</span><div class="pending" style="top:29px">Pending</div></div>
  <div class="row" style="top:285px;height:64px"><span style="left:12px;top:36px">Ivo Brandt</span><span style="left:242px;top:36px">8.04 km away</span><span style="left:546px;top:36px">-</span><div class="pending" style="top:29px">Pending</div></div>
  <div class="row" style="top:349px;height:64px"><span style="left:12px;top:34px">Niall Corden</span><span style="left:240px;top:34px">11.30 km away</span><span style="left:548px;top:34px">-</span><div class="pending" style="top:29px">Pending</div></div>
</section>

<div class="rule" style="top:1052px"></div>
<div class="footer">© 2017 Haulbeam . All rights reserved.</div>
</body>
</html>
```